Homemaking training schools needs a Business Card design

Designer, Hello!

No special requirements, good-looking enough.
--------------------------------------------------------------------------

Name: Marcus Dole
Chairman
Tel: 0574-71948263
Mobile: 13857420916
Email: kelvora@mailnest.example
Web: www.prt2019.example
Add: No.258, LanpingJie, BeiyuanQu, Ningbo, Zhejiang

LOGO
Ningbo PRT Homemaking Training School

Target Market(s)

pregnant women, mothers, infants, the elderly and families, including cleaning, cooking, nursing training.

Industry/Entity Type

Business

Contact Information for Business Card

Name: Marcus Dole
Chairman
Tel: 0574-71948263
Mobile: 13857420916
Email: kelvora@mailnest.example
Web: www.prt2019.example

LOGO

Font styles to use
Serif
Sans Serif
Decorative

Requirements
Nice to have
• Feels: clean, specifications, safety, comfort, warmth and happiness.

```html
<!DOCTYPE html>
<html lang="en">
<head>
<meta charset="utf-8">
<title>PeiRenTang Business Card</title>
<link rel="stylesheet" href="https://fonts.googleapis.com/css2?family=Montserrat:wght@500;600;800&family=Quicksand:wght@500;700&display=swap">
<style>
  :root {
    --brand-blue: #1275bf;
    --brand-pink: #e8128c;
    --paper: #ffffff;
    --stage: #2b2b2d;
  }
  * { margin: 0; padding: 0; box-sizing: border-box; }
  html, body { width: 1200px; height: 900px; overflow: hidden; }
  body {
    background: var(--stage);
    font-family: "Montserrat", sans-serif;
    position: relative;
  }
  .card {
    position: absolute;
    left: 260px;
    width: 680px;
    height: 390px;
    border-radius: 26px;
    overflow: hidden;
  }
  .card-back { top: 45px; background: var(--brand-blue); }
  .card-front { top: 465px; background: var(--paper); }

  /* Back */
  .back-strip {
    position: absolute; left: 0; right: 0; bottom: 0; height: 36px;
    background: var(--paper);
  }
  .back-strip .accent {
    position: absolute; left: 320px; width: 210px; top: 0; bottom: 0;
    background: var(--brand-pink);
  }
  .back-brand {
    position: absolute; left: 170px; top: 150px;
    display: flex; align-items: center; gap: 16px;
  }
  .brand-dot {
    width: 46px; height: 46px; border-radius: 50%;
    background: var(--brand-pink);
  }
  .back-brand .brand-name {
    font-family: "Quicksand", sans-serif; font-weight: 700;
    font-size: 46px; color: var(--paper);
  }
  .back-web {
    position: absolute; left: 236px; top: 222px;
    font-weight: 600; font-size: 20px; color: var(--paper);
    letter-spacing: 0.5px;
  }

  /* Front */
  .holder {
    position: absolute; right: 40px; top: 36px; text-align: right;
  }
  .holder-name {
    font-weight: 800; font-size: 30px; color: var(--brand-blue);
    letter-spacing: 0.5px; line-height: 1;
  }
  .holder-title {
    font-weight: 600; font-size: 13px; color: var(--brand-pink);
    letter-spacing: 1px; margin-top: 4px;
  }
  .holder-rule {
    position: absolute; right: 150px; top: 92px; width: 490px;
    height: 1.5px; background: var(--brand-blue);
  }
  .address {
    position: absolute; right: 40px; top: 128px; text-align: right;
    font-weight: 500; font-size: 15px; line-height: 1.45;
    color: var(--brand-blue);
  }
  .contacts {
    position: absolute; right: 36px; top: 200px; list-style: none;
  }
  .contacts li {
    display: flex; justify-content: flex-end; align-items: center; gap: 8px;
    font-weight: 600; font-size: 15px; line-height: 1.5;
    color: var(--brand-blue);
  }
  .contacts svg { width: 13px; height: 13px; flex: none; }
  .front-brand {
    position: absolute; left: 36px; top: 270px;
    display: flex; align-items: center; gap: 12px;
  }
  .front-brand .brand-dot { width: 30px; height: 30px; }
  .front-brand .brand-name {
    font-family: "Quicksand", sans-serif; font-weight: 700;
    font-size: 42px; color: var(--brand-blue);
  }
  .front-band {
    position: absolute; left: 0; right: 0; bottom: 0; height: 30px;
    background: var(--brand-blue);
  }
  .front-band .accent {
    position: absolute; left: 300px; width: 220px; top: 0; bottom: 0;
    background: var(--brand-pink);
  }
</style>
</head>
<body>
  <section class="card card-back" aria-label="Card back">
    <div class="back-brand">
      <span class="brand-dot"></span>
      <span class="brand-name">PeiRenTang</span>
    </div>
    <p class="back-web">www.prt2019.example</p>
    <div class="back-strip"><span class="accent"></span></div>
  </section>

  <section class="card card-front" aria-label="Card front">
    <div class="holder">
      <p class="holder-name">MARCUS DOLE</p>
      <p class="holder-title">CHAIRMAN</p>
    </div>
    <div class="holder-rule"></div>
    <p class="address">258, LanpingJie<br>BeiyuanQu, Ningbo, Zhejiang</p>
    <ul class="contacts">
      <li>0574-71948263
        <svg viewBox="0 0 16 16"><path d="M3 1.5l3 .5 1 3.5-2 1.2a9 9 0 004.3 4.3l1.2-2 3.5 1 .5 3-2 1.5C7 14.5 1.5 9 1.5 3.5z" fill="var(--brand-pink)"/></svg>
      </li>
      <li>13857420916
        <svg viewBox="0 0 16 16"><rect x="4" y="1" width="8" height="14" rx="1.5" fill="none" stroke="var(--brand-pink)" stroke-width="1.6"/><circle cx="8" cy="12.3" r="0.9" fill="var(--brand-pink)"/></svg>
      </li>
      <li>kelvora@mailnest.example
        <svg viewBox="0 0 16 16"><rect x="1.5" y="3.5" width="13" height="9" rx="1" fill="none" stroke="var(--brand-pink)" stroke-width="1.6"/><path d="M2 4l6 5 6-5" fill="none" stroke="var(--brand-pink)" stroke-width="1.6"/></svg>
      </li>
      <li>www.prt2019.example
        <svg viewBox="0 0 16 16"><circle cx="8" cy="8" r="6.5" fill="none" stroke="var(--brand-pink)" stroke-width="1.5"/><ellipse cx="8" cy="8" rx="2.8" ry="6.5" fill="none" stroke="var(--brand-pink)" stroke-width="1.2"/><path d="M1.5 8h13M3 4.5h10M3 11.5h10" stroke="var(--brand-pink)" stroke-width="1.1"/></svg>
      </li>
    </ul>
    <div class="front-brand">
      <span class="brand-dot"></span>
      <span class="brand-name">PeiRenTang</span>
    </div>
    <div class="front-band"><span class="accent"></span></div>
  </section>
</body>
</html>
```